New Corporate Email footer (business card design) for 40th Anniversary for Timber Traders

We are traders in sustainable timber worldwide, specialising in tropical hardwoods.
We need to keep our current company logo, but update our email footer with a business card like design which marks the company's 40th Anniversary. 1981-2021. We would need:
Company Logo, Name and Address, website
Sender's: Name, Tel no, fax no, email address
We would need this in a format which we could update ourselves re names/phone numbers if any change.

Target Market(s)

Customers, suppliers, service providers

Contact Information for Business Card

Mavis Thorne
Tel: +44 (0) 208 473 2586
Fax: +44 (0) 208 473 5820
Email: mavis@pwlwoods.co.uk
Web: www.pwlwoods.co.uk

PWL Woods Ltd. 7 Falcon Court, Birchmore Way, Oakwick, Surrey CR4 6TJ, UNITED KINGDOM

IMPORTANT NOTICE - This message contains confidential information for the intended addressee only. Any views expressed are those of the sender not PWL Woods Ltd unless otherwise stated. If you receive this message [and any attachment(s)] in error you must not store, copy, disclose or otherwise use any part of it and should advise the sender immediately on 020 8473 9152. Internet communications are not guaranteed secure or virus free. PWL reserves the right to monitor all e-mail communications and does not accept responsibility for any loss or damage resulting from access of this e-mail or any file(s) attached.

Font styles to use
Sans Serif
Other font styles liked:
• not actually sure

Requirements
Must have
• mention of company's 40th Anniversary 1981-2021, which is the whole point of the design
Nice to have
• Our company colour is British Racing Green, but any green theme may be good
Maybe a tree design but allowing the company logo to stand out.

```html
<!DOCTYPE html>
<html lang="en">
<head>
<meta charset="utf-8">
<title>PWL Woods – 40th Anniversary Email Footer</title>
<link href="https://fonts.googleapis.com/css2?family=Lato:wght@400;700&display=swap" rel="stylesheet">
<style>
  :root {
    --page-bg: #dcdcdc;
    --card-bg: #ffffff;
    --racing-green: #26312a;
    --text-dark: #1e1e1e;
    --divider: #c8c8c8;
    --notice-text: #ffffff;
    --gold-light: #f4d77a;
    --gold-mid: #c99a2e;
    --gold-dark: #7a5a14;
    --social-1: #2f4a3a;
    --social-2: #3d6b4f;
    --social-3: #5a8c6c;
  }
  * { margin: 0; padding: 0; box-sizing: border-box; }
  html, body {
    width: 1200px; height: 756px; overflow: hidden;
    background: var(--page-bg);
    font-family: "Lato", Arial, sans-serif;
  }
  .email-footer {
    position: absolute; left: 142px; top: 221px;
    width: 938px; height: 326px;
    background: var(--card-bg);
    box-shadow: 0 3px 6px rgba(0,0,0,0.28);
  }
  .company-mark {
    position: absolute; left: 62px; top: 28px; width: 110px;
    display: flex; flex-direction: column; align-items: center;
  }
  .company-mark__circle {
    width: 96px; height: 96px; border-radius: 50%;
    background: var(--racing-green);
  }
  .company-mark__name {
    margin-top: 12px;
    font-weight: 700; font-size: 34px; line-height: 1;
    color: var(--racing-green); letter-spacing: 1px;
  }
  .divider {
    position: absolute; width: 1px; background: var(--divider);
  }
  .divider--left { left: 197px; top: 37px; height: 153px; }
  .divider--mid { left: 527px; top: 37px; height: 153px; }
  .divider--date { left: 716px; top: 163px; height: 27px; background: #8a8a8a; }
  .sender-name {
    position: absolute; left: 221px; top: 30px;
    font-weight: 700; font-size: 25px; color: var(--text-dark);
  }
  .contact-list { position: absolute; left: 224px; top: 80px; list-style: none; }
  .contact-list li {
    display: flex; align-items: center; height: 28.5px;
    font-size: 21px; color: var(--text-dark);
  }
  .contact-list svg { width: 19px; height: 19px; margin-right: 7px; fill: var(--text-dark); flex: none; }
  .social-links {
    position: absolute; left: 585px; top: 164px; display: flex; gap: 4px;
  }
  .social-links span {
    width: 27px; height: 27px; border-radius: 50%; display: block;
  }
  .social-links .social--one { background: var(--social-1); }
  .social-links .social--two { background: var(--social-2); }
  .social-links .social--three { background: var(--social-3); }
  .anniversary-seal {
    position: absolute; left: 736px; top: 22px;
    width: 136px; height: 136px; border-radius: 50%;
    background: radial-gradient(circle at 45% 40%, var(--gold-light) 0%, var(--gold-mid) 55%, var(--gold-dark) 100%);
  }
  .anniversary-years {
    position: absolute; left: 744px; top: 165px;
    font-weight: 700; font-size: 22px; color: var(--text-dark);
  }
  .legal-notice {
    position: absolute; left: 0; bottom: 0; width: 100%; height: 117px;
    background: var(--racing-green); color: var(--notice-text);
    font-size: 14.4px; line-height: 19px; text-align: center;
    padding-top: 12px; white-space: nowrap;
  }
</style>
</head>
<body>
  <div class="email-footer">
    <div class="company-mark">
      <div class="company-mark__circle"></div>
      <div class="company-mark__name">PWL</div>
    </div>

    <div class="divider divider--left"></div>

    <div class="sender-name">Mavis Thorne</div>
    <ul class="contact-list">
      <li>
        <svg viewBox="0 0 24 24" aria-label="Telephone"><path d="M6.6 10.8a15.1 15.1 0 0 0 6.6 6.6l2.2-2.2c.3-.3.7-.4 1-.2 1.1.4 2.3.6 3.6.6.6 0 1 .4 1 1V20c0 .6-.4 1-1 1A17 17 0 0 1 3 4c0-.6.4-1 1-1h3.5c.6 0 1 .4 1 1 0 1.3.2 2.5.6 3.6.1.3 0 .7-.2 1z"/></svg>
        +44 (0) 208 473 2586
      </li>
      <li>
        <svg viewBox="0 0 24 24" aria-label="Fax"><path d="M6 2h12v5H6zM4 8h16a2 2 0 0 1 2 2v7h-4v5H6v-5H2v-7a2 2 0 0 1 2-2zm4 8v4h8v-4z"/></svg>
        +44 (0) 208 473 5820
      </li>
      <li>
        <svg viewBox="0 0 24 24" aria-label="Email"><path d="M2 5h20v14H2zm2 2v.5l8 5 8-5V7l-8 5z"/></svg>
        mavis@pwlwoods.co.uk
      </li>
      <li>
        <svg viewBox="0 0 24 24" aria-label="Website"><path d="M12 2a10 10 0 1 0 0 20 10 10 0 0 0 0-20zm6.9 6h-3a15 15 0 0 0-1.3-3.9A8 8 0 0 1 18.9 8zM12 4c.8 1.1 1.5 2.5 1.9 4h-3.8c.4-1.5 1.1-2.9 1.9-4zM4.3 14a8 8 0 0 1 0-4h3.4a16 16 0 0 0 0 4zm.8 2h3a15 15 0 0 0 1.3 3.9A8 8 0 0 1 5.1 16zm3-8h-3a8 8 0 0 1 4.3-3.9C8.8 5.3 8.4 6.6 8.1 8zM12 20c-.8-1.1-1.5-2.5-1.9-4h3.8c-.4 1.5-1.1 2.9-1.9 4zm2.3-6H9.7a14 14 0 0 1 0-4h4.6a14 14 0 0 1 0 4zm.3 5.9c.6-1.2 1-2.5 1.3-3.9h3a8 8 0 0 1-4.3 3.9zm1.7-5.9a16 16 0 0 0 0-4h3.4a8 8 0 0 1 0 4z"/></svg>
        www.pwlwoods.co.uk
      </li>
    </ul>

    <div class="divider divider--mid"></div>

    <div class="social-links">
      <span class="social--one" role="img" aria-label="Social network link"></span>
      <span class="social--two" role="img" aria-label="Video channel link"></span>
      <span class="social--three" role="img" aria-label="Microblog link"></span>
    </div>

    <div class="anniversary-seal" role="img" aria-label="Gold seal celebrating the company's 40th anniversary"></div>
    <div class="divider divider--date"></div>
    <div class="anniversary-years">1981-2021</div>

    <div class="legal-notice">
      IMPORTANT NOTICE - This message contains confidential information for the intended addressee only. Any views expressed are<br>
      those of the sender not PWL Woods Ltd unless otherwise stated. If you receive this message [and any attachment(s)] in error<br>
      you must not store, copy, disclose or otherwise use any part of it and should advise the sender immediately on 020 8473 9152.<br>
      Internet communications are not guaranteed secure or virus free. PWL reserves the right to monitor all e-mail communications<br>
      and does not accept responsibility for any loss or damage resulting from access of this e-mail or any file(s) attached.
    </div>
  </div>
</body>
</html>
```